Corvel Capital LLC

Need Professional Business cards for New Investment Fund

Target Market(s)

High Quality investors

Industry/Entity Type

Financial

Contact Information for Business Card

Phone Number +1 555 284 6190
Name Lukas Varenko
Title Fund Manager
email lv@FundCorvel.com
Website www.FundCorvel.com

Colors

Designer to choose colors to be used in the design.

Requirements
Must have
• Must have our Logo and all of the above. Must be made so lettering and loge can be raised

```html
<!DOCTYPE html>
<html lang="en">
<head>
<meta charset="UTF-8">
<title>Talvenor – Business Cards</title>
<link rel="stylesheet" href="https://fonts.googleapis.com/css2?family=Jost:wght@500;600&family=Raleway:wght@400;500&display=swap">
<style>
  :root {
    --backdrop: #1f1f1f;
    --card: #434f42;
    --card-edge: #ffffff;
    --accent: #5cbf48;
    --text-light: #ffffff;
    --text-soft: #e6e9e4;
  }
  * { margin: 0; padding: 0; box-sizing: border-box; }
  html, body {
    width: 1200px; height: 900px; overflow: hidden;
    background: var(--backdrop);
  }
  .canvas {
    position: relative; width: 1200px; height: 900px;
    background: radial-gradient(ellipse at 60% 30%, #383838 0%, var(--backdrop) 70%);
  }
  .card {
    position: absolute; left: 310px; width: 580px; height: 330px;
    background: var(--card);
    box-shadow: 0 18px 40px rgba(0,0,0,0.55);
  }
  .card--front { top: 80px; border-top: 4px solid var(--card-edge); border-bottom: 4px solid var(--card-edge); }
  .card--back { top: 480px; }

  .brand {
    position: absolute; display: flex; align-items: center; gap: 12px;
    font-family: "Jost", sans-serif; font-weight: 600;
    color: var(--text-light); letter-spacing: 0.06em; white-space: nowrap;
  }
  .brand__square { background: var(--accent); flex: none; }
  .card--front .brand { left: 50%; top: 50%; transform: translate(-50%, -50%); font-size: 40px; }
  .card--front .brand__square { width: 32px; height: 32px; }
  .card--back .brand { left: 40px; top: 56px; font-size: 28px; }
  .card--back .brand__square { width: 22px; height: 22px; }

  .divider {
    position: absolute; left: 40px; right: 40px; top: 165px;
    height: 1.5px; background: var(--accent);
  }
  .holder { position: absolute; left: 40px; top: 182px; }
  .holder__name {
    font-family: "Jost", sans-serif; font-weight: 600; font-size: 23px;
    color: var(--text-light); letter-spacing: 0.03em; text-transform: uppercase;
  }
  .holder__title {
    font-family: "Raleway", sans-serif; font-weight: 400; font-size: 17px;
    color: var(--text-soft); margin-top: 2px;
  }
  .contact {
    position: absolute; right: 40px; top: 200px; list-style: none;
    font-family: "Raleway", sans-serif; font-weight: 400; font-size: 17px;
    color: var(--text-light);
  }
  .contact__item {
    display: flex; justify-content: flex-end; align-items: center;
    gap: 14px; height: 30px; white-space: nowrap;
  }
  .contact__icon { width: 16px; height: 16px; flex: none; }
  .accent-bar {
    position: absolute; left: 40px; bottom: 0; width: 190px; height: 5px;
    background: var(--accent);
  }
</style>
</head>
<body>
<main class="canvas">
  <section class="card card--front" aria-label="Card front">
    <div class="brand"><span class="brand__square"></span><span class="brand__name">TALVENOR</span></div>
  </section>

  <section class="card card--back" aria-label="Card back">
    <div class="brand"><span class="brand__square"></span><span class="brand__name">TALVENOR</span></div>
    <div class="divider"></div>
    <div class="holder">
      <p class="holder__name">Lukas Varenko</p>
      <p class="holder__title">Title Fund Manager</p>
    </div>
    <ul class="contact">
      <li class="contact__item">+1 555 284 6190
        <svg class="contact__icon" viewBox="0 0 16 16" aria-hidden="true"><path d="M4 1.5l2.2 3-1.3 1.6c.8 1.8 2.2 3.2 4 4l1.6-1.3 3 2.2-1.3 2.4C7 13.4 2.6 9 2 3z" fill="#5cbf48"/></svg>
      </li>
      <li class="contact__item">lv@FundCorvel.com
        <svg class="contact__icon" viewBox="0 0 16 16" aria-hidden="true"><rect x="1.5" y="3.5" width="13" height="9" fill="none" stroke="#5cbf48" stroke-width="1.4"/><path d="M1.5 3.5L8 9l6.5-5.5" fill="none" stroke="#5cbf48" stroke-width="1.4"/></svg>
      </li>
      <li class="contact__item">www.FundCorvel.com
        <svg class="contact__icon" viewBox="0 0 16 16" aria-hidden="true"><g fill="none" stroke="#5cbf48" stroke-width="1.2"><circle cx="8" cy="8" r="6.5"/><ellipse cx="8" cy="8" rx="3" ry="6.5"/><path d="M1.5 8h13M2.5 4.8h11M2.5 11.2h11"/></g></svg>
      </li>
    </ul>
    <div class="accent-bar"></div>
  </section>
</main>
</body>
</html>
```